Allied Health team of Physiotherapists & Occupational Therapists seek a business card design

We have our new logo, we now need our new business cards and stationary. Tidewell: Oedema & Family Clinic is seeking a generic card design to represent our whole team and individual cards for each therapist that incorporates our new logo to communicate our holistic approach that is calming, nuturing, supportive and welcoming.
Our Physiotherapists and Occupational Therapists assess, treat and provide education for people who are at risk of or who have lymphoedema. This is often as a result of treatment for cancer. We provide pre-operative and post-operative management and cancer rehabilitation in our Pilates studio. Our team also consists of Physiotherapists who have a strong interest in pelvic floor and continence management for both men and women.

Target Market(s)

Mainly women health conscious

Industry/Entity Type

Allied Health: Physiotherapy / Occupational Therapy

Contact Information for Business Card

Address: 14 Gallivant Ave Marlow Bay 3288 Phone: 84316570 fax: 8431 6578 Email: info@tidewellcareservices.com.au Website: tidewellcareservices.com.au Facebook address: circlepage.net/TidewellOedemaAndFamilyCareClinic. Room to write appointments. Individual cards need to have name, office email and individual email and professional details

Requirements
Must have
• Logo as per uploaded documents

```html
<!DOCTYPE html>
<html lang="en">
<head>
<meta charset="utf-8">
<title>Tidewell: Oedema &amp; Family Clinic – Business Cards</title>
<link href="https://fonts.googleapis.com/css2?family=Lora:wght@500&family=Fira+Sans:ital,wght@0,300;1,300&display=swap" rel="stylesheet">
<style>
  :root {
    --page-bg: #e9e9e9;
    --peach: #f9ae7e;
    --peach-soft: #fbd9c2;
    --sage: #e6ebe6;
    --white: #ffffff;
    --ink: #4a4a4a;
    --ink-soft: #555555;
  }
  * { box-sizing: border-box; margin: 0; padding: 0; }
  html, body { width: 1133px; height: 1200px; overflow: hidden; }
  body {
    background: var(--page-bg);
    position: relative;
    font-family: "Fira Sans", sans-serif;
    font-weight: 300;
    color: var(--ink);
  }
  .card {
    position: absolute;
    left: 219px;
    width: 693px;
    height: 397px;
  }
  /* Appointment side */
  .card--appointment { top: 152px; background: var(--peach); }
  .appointment__title {
    position: absolute; left: 116px; top: 104px;
    font-family: "Lora", serif; font-weight: 500;
    font-size: 23px; line-height: 30px; color: var(--white);
  }
  .appointment__label {
    position: absolute; font-size: 15px; color: var(--ink-soft);
    line-height: 32px;
  }
  .appointment__field {
    position: absolute; height: 32px; background: var(--white); border-radius: 6px;
  }
  .social {
    position: absolute; left: 116px; top: 267px;
    display: flex; align-items: center; gap: 7px;
    font-size: 18px; line-height: 22px; color: var(--ink-soft);
  }
  .social__dot { width: 15px; height: 15px; border-radius: 50%; background: var(--white); flex: none; }

  /* Contact side */
  .card--contact { top: 647px; background: var(--white); }
  .leaf-decor {
    position: absolute; left: 0; top: 36px; width: 320px; height: 94px;
    background: linear-gradient(90deg, rgba(251,217,194,0.25), rgba(230,235,230,0.6) 50%, rgba(230,235,230,0));
    border-radius: 0 160px 0 0;
  }
  .signature {
    position: absolute; left: 21px; top: 140px; width: 270px; height: 44px;
    background: linear-gradient(90deg, var(--peach-soft), rgba(251,217,194,0.35));
    border-radius: 22px;
  }
  .credentials { position: absolute; left: 35px; top: 186px; line-height: 1.2; }
  .credentials__item { font-style: italic; font-size: 13.7px; color: var(--ink-soft); }
  .credentials__role { font-size: 16px; color: var(--ink-soft); margin-top: 1px; }
  .contact-list {
    position: absolute; left: 35px; top: 258px; list-style: none;
    font-size: 16px; color: var(--ink-soft);
  }
  .contact-list li { display: flex; align-items: center; height: 17.8px; gap: 8px; }
  .contact-list svg { width: 14px; height: 14px; flex: none; }
  .brand {
    position: absolute; left: 431px; top: 80px; width: 224px;
    text-align: center;
    font-family: "Lora", serif; font-weight: 500;
    color: var(--peach); font-size: 22px; line-height: 1.35;
  }
  .brand__name { font-size: 46px; display: block; line-height: 1.2; }
</style>
</head>
<body>

<section class="card card--appointment" aria-label="Appointment card">
  <h2 class="appointment__title">Next Appointment</h2>
  <span class="appointment__label" style="left:116px;top:154px;">Name&nbsp;&nbsp;:</span>
  <div class="appointment__field" style="left:182px;top:154px;width:394px;"></div>
  <span class="appointment__label" style="left:116px;top:192px;">Date&nbsp;&nbsp;&nbsp;&nbsp;:</span>
  <div class="appointment__field" style="left:182px;top:192px;width:190px;"></div>
  <span class="appointment__label" style="left:385px;top:192px;">Time&nbsp;&nbsp;:</span>
  <div class="appointment__field" style="left:445px;top:192px;width:131px;"></div>
  <p class="social"><span class="social__dot"></span>circlepage.net/TidewellOedemaAndFamilyCareClinic</p>
</section>

<section class="card card--contact" aria-label="Therapist contact card">
  <div class="leaf-decor" role="img" aria-label="Faint decorative leaf branch"></div>
  <div class="signature" role="img" aria-label="Handwritten signature of Marissa Hale"></div>
  <div class="credentials">
    <p class="credentials__item">B. Physio</p>
    <p class="credentials__item">Post Grad Certif. Continence &amp; Pelvic Floor Rehabilitation</p>
    <p class="credentials__role">Physiotherapist Pelvic Health</p>
  </div>
  <ul class="contact-list">
    <li><svg viewBox="0 0 14 14"><circle cx="7" cy="7" r="7" fill="#f9ae7e"/><path d="M4 5.5c0-1 6-1 6 0v.6H8.6v-.5H5.4v.5H4z M4.5 7h5v2.5h-5z" fill="#fff"/></svg>84316570 Phone</li>
    <li><svg viewBox="0 0 14 14"><circle cx="7" cy="7" r="7" fill="#f9ae7e"/><path d="M5 3.5h4v2H5z M3.5 6h7v3.5h-7z M5 8.5h4v2H5z" fill="#fff"/></svg>8431 6578 Fax</li>
    <li><svg viewBox="0 0 14 14"><circle cx="7" cy="7" r="7" fill="#f9ae7e"/><rect x="3.5" y="4.5" width="7" height="5" fill="#fff"/><path d="M3.5 4.5L7 7.3l3.5-2.8" stroke="#f9ae7e" stroke-width="0.8" fill="none"/></svg>marissa@tidewellcareservices.com.au</li>
    <li><svg viewBox="0 0 14 14"><circle cx="7" cy="7" r="7" fill="#f9ae7e"/><rect x="3.5" y="4.5" width="7" height="5" fill="#fff"/><path d="M3.5 4.5L7 7.3l3.5-2.8" stroke="#f9ae7e" stroke-width="0.8" fill="none"/></svg>info@tidewellcareservices.com.au (office)</li>
    <li><svg viewBox="0 0 14 14"><circle cx="7" cy="7" r="7" fill="#f9ae7e"/><circle cx="7" cy="7" r="3.4" fill="none" stroke="#fff" stroke-width="1"/><path d="M3.6 7h6.8M7 3.6v6.8" stroke="#fff" stroke-width="0.8"/></svg>tidewellcareservices.com.au</li>
    <li><svg viewBox="0 0 14 14"><circle cx="7" cy="7" r="7" fill="#f9ae7e"/><path d="M7 3.2L3 6.8h1.2v3.6h2V8.4h1.6v2h2V6.8H11z" fill="#fff"/></svg>14 Gallivant Ave, Marlow Bay 3288</li>
  </ul>
  <p class="brand"><span class="brand__name">Tidewell:</span>Oedema &amp; Family Clinic</p>
</section>

</body>
</html>
```